Design concept for BrightKestrel.com Support Page

We are about to launch a new support page for our www.brightkestrel.com service for photographers and visual artists. The service provides media management, cloud storage, promotional and secure distribution to our members.

The support page will include FAQs and video tutorials.

In particular we're looking for a header for this page that suggests the user is in the support area of our service - so perhaps an illustration that suggests support could look nice (perhaps repair man or doctor iconography). Something to give this area of our site a different look and something that looks both cool and friendly.

Currently the page looks distinctly sparse and undesigned (see attached screenshot) - something that could be remedied, we feel, by some subtle design enhancements that we can implement using CSS.

```html
<!DOCTYPE html>
<html lang="en">
<head>
<meta charset="utf-8">
<title>BrightKestrel Support</title>
<link rel="stylesheet" href="https://fonts.googleapis.com/css2?family=Open+Sans:wght@400;600;700&family=Roboto+Condensed:wght@700&display=swap">
<style>
:root{
  --orange:#f26f21;
  --orange-light:#f7a04a;
  --ink:#333;
  --muted:#777;
  --line:#e2e2e2;
  --card:#f7f7f7;
  --card-border:#dcdcdc;
  --active:#8c8c8c;
  --section:#f4f4f4;
  --footer:#000;
}
*{box-sizing:border-box;margin:0;padding:0}
html,body{width:742px;height:1200px;overflow:hidden;background:#fff}
body{position:relative;font-family:"Open Sans",Arial,sans-serif;color:var(--ink)}
.abs{position:absolute}

/* header */
.site-header{left:0;top:0;width:742px;height:62px}
.brand{left:62px;top:16px;display:flex;align-items:center;gap:7px}
.brand-mark{width:24px;height:24px;background:var(--orange);border-radius:4px}
.brand-name{font-weight:700;font-size:22px;color:#555;letter-spacing:-.3px}
.search{left:405px;top:18px;width:180px;height:21px;border:1px solid #ddd;border-radius:2px;display:flex;align-items:center;justify-content:space-between;padding:0 2px 0 9px}
.search-field{font-size:8.5px;color:#999}
.search-btn{background:var(--orange);color:#fff;font-size:8px;font-weight:600;padding:3px 6px;border-radius:2px}
.user{left:602px;top:16px;display:flex;align-items:center;gap:8px;font-size:8.5px}
.avatar{width:24px;height:24px;border-radius:50%;background:#b9b2ab}

/* hero */
.hero{left:0;top:62px;width:742px;height:156px;background:linear-gradient(90deg,var(--orange) 0%,var(--orange) 55%,var(--orange-light) 75%,var(--orange) 100%)}
.hero-title{left:63px;top:35px;font-size:34px;font-weight:400;color:#fff;line-height:1}
.hero-sub{left:63px;top:78px;font-size:22px;font-weight:600;color:#fde3c6;line-height:1}
.hero-art{left:488px;top:6px;width:160px;height:136px;border-radius:6px;background:linear-gradient(160deg,#3a3a3a 0%,#f5b46a 60%,#f7a04a 100%);opacity:.55}

/* intro */
.intro{left:62px;top:242px;width:618px;text-align:center;font-size:11.5px;line-height:17px;color:var(--muted)}
.divider{left:62px;top:303px;width:618px;height:1px;background:var(--line)}

/* faq */
.section-title{font-weight:400;color:var(--orange)}
.faq-title{left:62px;top:332px;font-size:21px}
.faq{left:62px;width:618px;height:109px;background:var(--card);border:1px solid var(--card-border);padding:16px 20px 0 18px}
.faq-head{display:flex;align-items:center;gap:7px;font-family:Arial,Helvetica,sans-serif;font-size:12px;color:var(--orange)}
.faq-icon{width:20px;height:20px;border-radius:50%;background:var(--orange);color:#fff;font-size:11px;font-weight:700;display:flex;align-items:center;justify-content:center}
.faq-body{margin:6px 0 0 27px;font-family:Arial,Helvetica,sans-serif;font-size:7.2px;line-height:16px;color:#666}
.faq.is-open{background:var(--active);border-color:var(--active)}
.faq.is-open .faq-head,.faq.is-open .faq-body{color:#fff}
.faq.is-open .faq-icon{background:#fff;color:var(--orange)}
.btn-all{left:586px;top:844px;width:94px;height:21px;background:var(--orange);border-radius:2px;color:#fff;font-family:"Roboto Condensed",Arial,sans-serif;font-weight:700;font-size:9px;display:flex;align-items:center;justify-content:center}

/* videos */
.videos{left:0;top:897px;width:742px;height:209px;background:var(--section)}
.videos-title{left:0;top:920px;width:742px;text-align:center;font-size:24px}
.tile{top:967px;width:142px}
.thumb{height:87px;display:flex;align-items:center;justify-content:center}
.caption{margin-top:7px;text-align:center;font-size:8.5px;line-height:13px;color:#333}
.arrow{top:978px;width:36px;height:45px;background:#d6d6d6;display:flex;align-items:center;justify-content:center}

/* footer */
.site-footer{left:0;top:1106px;width:742px;height:94px;background:var(--footer);text-align:center}
.foot-nav{margin-top:20px;font-size:8.5px;color:#bbb}
.foot-nav span{margin:0 5px}
.copy{margin-top:14px;font-size:8.5px;color:#eee}
.powered{margin-top:2px;font-size:8px;color:#777}
</style>
</head>
<body>

<header class="site-header abs">
  <div class="brand abs"><span class="brand-mark"></span><span class="brand-name">BrightKestrel</span></div>
  <div class="search abs"><span class="search-field">Search</span><span class="search-btn">SEARCH</span></div>
  <div class="user abs"><span class="avatar"></span><span>Mara Lindqvist</span></div>
</header>

<section class="hero abs">
  <h1 class="hero-title abs">We’re Happy To Help...</h1>
  <p class="hero-sub abs">BrightKestrel Support</p>
  <div class="hero-art abs" role="img" aria-label="Illustration of a repairman with a wrench and a cheerful office worker on a chair"></div>
</section>

<p class="intro abs">Aliquam erat volutpat. Etiam luctus rutrum diam sit amet egestas. Mauris et odio nisl. Cras vulputate mi quis neque venenatis, vitae lacinia magna euismod. Aliquam tincidunt velit et diam mattis iaculis.</p>
<div class="divider abs"></div>

<h2 class="section-title faq-title abs">Faq’s</h2>

<article class="faq is-open abs" style="top:374px">
  <div class="faq-head"><span class="faq-icon">?</span>Uploading files using the Drag and Drop Uploader</div>
  <p class="faq-body">It is a long established fact that a reader will be distracted by the readable content of a page when looking at its layout. The point of using Lorem Ipsum is that it has a more-or-less normal distribution of letters, as opposed to using 'Content here, content here', making it look like readable English. Many desktop publishing packages and web page editors now use Lorem Ipsum as their default model text, and a search for 'lorem ipsum' will uncover many web sites still in their infancy.</p>
</article>
<article class="faq abs" style="top:490px">
  <div class="faq-head"><span class="faq-icon">?</span>Uploading files using the Drag and Drop Uploader</div>
  <p class="faq-body">It is a long established fact that a reader will be distracted by the readable content of a page when looking at its layout. The point of using Lorem Ipsum is that it has a more-or-less normal distribution of letters, as opposed to using 'Content here, content here', making it look like readable English. Many desktop publishing packages and web page editors now use Lorem Ipsum as their default model text, and a search for 'lorem ipsum' will uncover many web sites still in their infancy.</p>
</article>
<article class="faq abs" style="top:606px">
  <div class="faq-head"><span class="faq-icon">?</span>Uploading files using the Drag and Drop Uploader</div>
  <p class="faq-body">It is a long established fact that a reader will be distracted by the readable content of a page when looking at its layout. The point of using Lorem Ipsum is that it has a more-or-less normal distribution of letters, as opposed to using 'Content here, content here', making it look like readable English. Many desktop publishing packages and web page editors now use Lorem Ipsum as their default model text, and a search for 'lorem ipsum' will uncover many web sites still in their infancy.</p>
</article>
<article class="faq abs" style="top:722px">
  <div class="faq-head"><span class="faq-icon">?</span>Uploading files using the Drag and Drop Uploader</div>
  <p class="faq-body">It is a long established fact that a reader will be distracted by the readable content of a page when looking at its layout. The point of using Lorem Ipsum is that it has a more-or-less normal distribution of letters, as opposed to using 'Content here, content here', making it look like readable English. Many desktop publishing packages and web page editors now use Lorem Ipsum as their default model text, and a search for 'lorem ipsum' will uncover many web sites still in their infancy.</p>
</article>

<a class="btn-all abs">VIEW ALL FAQ’S</a>

<section class="videos abs"></section>
<h2 class="section-title videos-title abs">Video Tutorials</h2>

<div class="arrow abs" style="left:0"><svg width="14" height="26" viewBox="0 0 14 26"><path d="M12 1 1 13l11 12" fill="none" stroke="#fff" stroke-width="1.5"/></svg></div>
<div class="arrow abs" style="left:706px"><svg width="14" height="26" viewBox="0 0 14 26"><path d="M2 1l11 12L2 25" fill="none" stroke="#fff" stroke-width="1.5"/></svg></div>

<div class="tile abs" style="left:62px">
  <div class="thumb" role="img" aria-label="Upload button with a pointing cursor" style="background:linear-gradient(180deg,#9fb3c2,#c9c9c9)">
    <svg width="30" height="30" viewBox="0 0 30 30"><circle cx="15" cy="15" r="13" fill="none" stroke="#fff" stroke-width="2.5"/><path d="M12 9v12l9-6z" fill="#fff"/></svg>
  </div>
  <p class="caption">Uploading Files Using the<br>Drang and Drop Uploader</p>
</div>
<div class="tile abs" style="left:221px">
  <div class="thumb" role="img" aria-label="People around a large tablet with colourful photos" style="background:linear-gradient(180deg,#d8d8d8,#b9a9a0)">
    <svg width="30" height="30" viewBox="0 0 30 30"><circle cx="15" cy="15" r="13" fill="none" stroke="#fff" stroke-width="2.5"/><path d="M12 9v12l9-6z" fill="#fff"/></svg>
  </div>
  <p class="caption">Publising Files</p>
</div>
<div class="tile abs" style="left:379px">
  <div class="thumb" role="img" aria-label="Person at a desk surrounded by gallery windows" style="background:linear-gradient(180deg,#5fa6a0,#4a8f8a)">
    <svg width="30" height="30" viewBox="0 0 30 30"><circle cx="15" cy="15" r="13" fill="none" stroke="#fff" stroke-width="2.5"/><path d="M12 9v12l9-6z" fill="#fff"/></svg>
  </div>
  <p class="caption">Creating Galleries</p>
</div>
<div class="tile abs" style="left:538px">
  <div class="thumb" role="img" aria-label="Colourful portfolio and business icons" style="background:linear-gradient(135deg,#2f6f8f,#e9a83a)">
    <svg width="30" height="30" viewBox="0 0 30 30"><circle cx="15" cy="15" r="13" fill="none" stroke="#fff" stroke-width="2.5"/><path d="M12 9v12l9-6z" fill="#fff"/></svg>
  </div>
  <p class="caption">Creating Portfolios</p>
</div>

<footer class="site-footer abs">
  <nav class="foot-nav">Home<span>•</span>Contact Us<span>•</span>Affiliate Program<span>•</span>Privacy Policy<span>•</span>Site Terms and Conditions<span>•</span>About Us</nav>
  <p class="copy">© Copyright 2014 Harbourline Images Pte Ltd. All rights reserved.</p>
  <p class="powered">Powered by BrightKestrel</p>
</footer>

</body>
</html>
```